Custom hot rod builder needs a website for launch of new business where he will build luxury garages

We need a website that gives a WOW first impression for "Summit Carports". This is a new business so photos are renderings but we need it to really attract a particular audience. Our initial business is custom hot rods so now we are building garages for them. These will be like luxury "homes" for cars! I will attach our new logo. Website needs to feel powerful and prestigious.

Target Market(s)

middle aged men, car enthusiasts

Industry/Entity Type

automotive, construction

Coding

Coded - Design and coding required

Number of Pages Required

2 page

Font styles to use
Serif

Colors
0054AA
0677BA
7BADD7
CADEEF
E8F1F8

Requirements
Must have
• a WOW factor. luxury. contact form.
Nice to have
• ?

```html
<!DOCTYPE html>
<html lang="en">
<head>
<meta charset="utf-8">
<title>Summit Carports</title>
<link rel="stylesheet" href="https://fonts.googleapis.com/css2?family=Mulish:wght@400;600;700&family=Michroma&family=Oswald:wght@500&display=swap">
<style>
:root{
  --blue-deep:#0054AA;
  --blue:#0677BA;
  --blue-bright:#29A8E0;
  --blue-soft:#7BADD7;
  --blue-pale:#CADEEF;
  --blue-mist:#E8F1F8;
  --ink:#333;
  --muted:#555;
  --line:#e2e2e2;
  --night:#000;
}
*{box-sizing:border-box;margin:0;padding:0}
html,body{width:1200px;height:3868px;overflow:hidden;background:#fff}
body{position:relative;font-family:"Mulish",sans-serif;color:var(--ink)}
.abs{position:absolute}
.btn{position:absolute;display:flex;align-items:center;justify-content:center;background:var(--blue-bright);color:#fff;font-size:16px;border-radius:3px}
.heading{font-family:"Michroma",sans-serif;color:var(--blue-deep);letter-spacing:3px;text-transform:uppercase}
.heading .lite{color:var(--blue-bright)}
.swoosh{position:absolute;width:60px;height:8px}

/* header */
.site-header{position:absolute;left:0;top:0;width:1200px;height:88px;background:#fff}
.brand{position:absolute;display:flex;align-items:center;gap:10px;font-weight:700;color:var(--blue)}
.brand .mark{border-radius:50%;background:var(--blue)}
.nav{position:absolute;top:34px;left:575px;display:flex;gap:26px;font-size:14px;color:#222}
.nav .active{color:var(--blue-bright)}
.nav-phone{position:absolute;left:852px;top:28px;display:flex;align-items:center;gap:8px;font-size:20px;color:var(--blue);border-left:1px solid #ccc;padding-left:12px;height:32px}

/* hero */
.hero{position:absolute;left:0;top:88px;width:1200px;height:610px;background:linear-gradient(160deg,#3a2a1e 0%,#6b4a2e 35%,#2f4b43 60%,#7a5a38 80%,#3b2b20 100%)}
.hero-title{position:absolute;left:0;width:1200px;top:110px;text-align:center;font-family:"Oswald",sans-serif;font-weight:500;font-size:42px;line-height:56px;color:#fff;text-shadow:0 2px 6px rgba(0,0,0,.6)}
.hero-arrow{position:absolute;top:262px;width:32px;height:32px;border:2px solid rgba(255,255,255,.85);border-radius:50%}
.hero-wave{position:absolute;left:0;top:540px}

/* welcome */
.welcome-photo{left:187px;top:555px;width:354px;height:496px;border-radius:20px;background:linear-gradient(180deg,#b8c3cc 0%,#9aa6ae 45%,#6d7a70 60%,#b9bcbf 80%,#8a8d90 100%)}
.welcome-copy{left:563px;top:730px;width:450px}
.welcome-copy p{font-size:12px;line-height:22.5px;color:var(--muted);margin-top:10px}

/* offers */
.offer{position:absolute;width:403px;height:114px;background:#fff;box-shadow:0 0 8px rgba(0,0,0,.12)}
.offer .icon{position:absolute;left:20px;top:27px;width:60px;height:60px;border-radius:50%;background:#fff;box-shadow:0 4px 10px rgba(0,0,0,.12);display:flex;align-items:center;justify-content:center}
.offer h3{position:absolute;left:92px;top:28px;font-size:14px;font-weight:600;color:var(--blue-deep)}
.offer p{position:absolute;left:92px;top:50px;width:290px;font-size:11px;line-height:20px;color:var(--muted)}

/* banner */
.banner{left:0;top:1532px;width:1200px;height:494px;background:linear-gradient(180deg,#30373d 0%,#4a5257 40%,#3a3431 70%,#2e3230 100%)}
.banner-title{position:absolute;left:0;width:1200px;text-align:center;font-family:"Michroma",sans-serif;color:#fff;font-size:30px;letter-spacing:4px;text-transform:uppercase;line-height:44px;top:1686px}

/* gallery */
.shot{position:absolute}

/* contact */
.contact-card{left:254px;top:2797px;width:692px;height:479px;background:#fff;box-shadow:0 0 14px rgba(0,0,0,.12)}
.contact-sub{position:absolute;left:254px;top:2902px;width:692px;text-align:center;font-size:19px;line-height:30px;color:#333}
.field{position:absolute;height:33px;border:1px solid #d6d6d6;font-size:10px;color:#555;display:flex;align-items:center;padding-left:28px}
.field svg{position:absolute;left:9px;top:11px}
.field.tall{height:84px;align-items:flex-start;padding-top:11px}

/* footer */
.footer{left:0;top:3380px;width:1200px;height:488px}
.foot-info{position:absolute;top:3683px;display:flex;align-items:center;gap:14px;color:#fff;font-size:14px;line-height:20px}
.foot-info .ring{width:44px;height:44px;border:1px solid #fff;border-radius:50%;display:flex;align-items:center;justify-content:center}
.social{position:absolute;top:3768px;width:28px;height:28px;border:1.5px solid #fff;border-radius:50%}
.rule{position:absolute;left:187px;width:826px;height:1px;background:#333}
</style>
</head>
<body>

<header class="site-header">
  <div class="brand" style="left:195px;top:26px;font-size:22px"><span class="mark" style="width:36px;height:36px"></span>SUMMIT CARPORTS</div>
  <nav class="nav"><span class="active">Home</span><span>Work Gallery</span><span>Contact Us</span></nav>
  <div class="nav-phone">
    <svg width="20" height="20" viewBox="0 0 24 24" fill="none" stroke="#0677BA" stroke-width="1.6"><path d="M5 3h4l2 5-2.5 1.5a11 11 0 0 0 6 6L16 13l5 2v4a2 2 0 0 1-2 2A17 17 0 0 1 3 5a2 2 0 0 1 2-2z"/></svg>
    123.456.7890
  </div>
</header>

<section class="hero" role="img" aria-label="Rendering of a luxury garage interior with classic hot rods and sports cars">
  <h1 class="hero-title">We Build Custom Hot Rod Luxury Garages</h1>
  <div class="btn" style="left:525px;top:182px;width:150px;height:40px">Contact Us Today</div>
  <div class="hero-arrow" style="left:91px"></div>
  <div class="hero-arrow" style="left:1081px"></div>
</section>
<svg class="hero-wave" width="1200" height="160" viewBox="0 0 1200 160">
  <path d="M0 100 C 200 30 380 30 600 70 C 820 110 1000 140 1200 90 L1200 160 L0 160Z" fill="#fff"/>
  <path d="M0 100 C 180 40 300 30 420 40 C 300 40 150 70 0 120Z" fill="#29A8E0"/>
  <path d="M560 60 C 780 120 1000 140 1200 90 L1200 110 C 1000 160 760 140 560 60Z" fill="#0054AA"/>
  <path d="M0 100 C 200 30 380 30 600 70 C 820 110 1000 140 1200 90" fill="none" stroke="#fff" stroke-width="6"/>
</svg>

<div class="abs welcome-photo" role="img" aria-label="Rendering of the garage exterior with palm trees and cars behind glass"></div>
<div class="abs welcome-copy">
  <h2 class="heading" style="font-size:26px;line-height:32px"><span class="lite">Welcome To</span><br><span class="lite">Summit</span> Carports</h2>
  <svg class="swoosh" style="position:static;display:block;margin:22px 0 6px" viewBox="0 0 60 8"><path d="M0 6 Q30 -2 60 4 Q30 2 0 8Z" fill="#0054AA"/></svg>
  <p>Lorem ipsum dolor sit amet, consectetuer adipiscing elit, sed dim nonummy nibh euismod tincidunt ut laoreet dolore magna aliquam erat volutpat. Ut wisi enim ad minim veniam, quis nostrud exerci.</p>
  <p>Lorem ipsum dolor sit amet, consectetuer adipiscing elit, sed dim nonummy nibh euismod tincidunt ut laoreet dolore magna aliquam erat volutpat. Ut wisi enim ad minim veniam, quis nostrud exerci tation ullamcorper suscipit lobortis nisl ut aliquip ex ea commodo consequat. Duis aute</p>
</div>
<div class="btn" style="left:563px;top:1008px;width:127px;height:42px">Contact Us</div>

<h2 class="heading abs" style="left:0;width:1200px;text-align:center;top:1128px;font-size:26px"><span class="lite">What We</span> Offer</h2>
<svg class="swoosh" style="left:570px;top:1162px" viewBox="0 0 60 8"><path d="M0 6 Q30 -2 60 4 Q30 2 0 8Z" fill="#0054AA"/></svg>

<div class="offer" style="left:187px;top:1202px"><div class="icon">
  <svg width="34" height="34" viewBox="0 0 34 34" fill="none" stroke="#0677BA" stroke-width="1.4" stroke-linejoin="round"><path d="M2 12l6-3 4 2 5-2 5 2 4-2 6 3"/><path d="M8 9v12M26 9v12"/><path d="M12 15l5 4 5-4"/><path d="M8 21l6 5 3-2 3 2 6-5"/></svg>
</div><h3>Loyalty Programs</h3><p>Lorem ipsum dolor sit amet, consectetuer adipiscing elit, sed dim nonummy nibh euismod.</p></div>
<div class="offer" style="left:607px;top:1202px"><div class="icon">
  <svg width="34" height="34" viewBox="0 0 34 34" fill="none" stroke="#0677BA" stroke-width="1.4" stroke-linejoin="round"><circle cx="17" cy="14" r="10"/><path d="M17 8l1.8 3.8 4 .5-3 2.8.8 4-3.6-2-3.6 2 .8-4-3-2.8 4-.5z"/><path d="M11 22l-2 9 4-2 2 3 2-8M23 22l2 9-4-2-2 3-2-8"/></svg>
</div><h3>20 Years Experience</h3><p>Lorem ipsum dolor sit amet, consectetuer adipiscing elit, sed dim nonummy nibh euismod.</p></div>
<div class="offer" style="left:187px;top:1337px"><div class="icon">
  <svg width="34" height="34" viewBox="0 0 34 34" fill="none" stroke="#0677BA" stroke-width="1.4" stroke-linejoin="round"><path d="M18 4h11v11L15 29 4 18z"/><circle cx="24" cy="9" r="2"/><path d="M13 17l5-5M14 21l5-5"/></svg>
</div><h3>Always The Best Value</h3><p>Lorem ipsum dolor sit amet, consectetuer adipiscing elit, sed dim nonummy nibh euismod.</p></div>
<div class="offer" style="left:607px;top:1337px"><div class="icon">
  <svg width="34" height="34" viewBox="0 0 34 34" fill="none" stroke="#0677BA" stroke-width="1.4" stroke-linejoin="round"><path d="M8 15a9 9 0 0 1 18 0"/><rect x="5" y="14" width="5" height="8" rx="2"/><rect x="24" y="14" width="5" height="8" rx="2"/><path d="M27 22c0 4-4 6-8 6h-2"/><path d="M6 32c1-4 5-6 11-6s10 2 11 6"/></svg>
</div><h3>24 Hour Customer Service Available</h3><p>Lorem ipsum dolor sit amet, consectetuer adipiscing elit, sed dim nonummy nibh euismod.</p></div>

<div class="abs banner" role="img" aria-label="Dusk rendering of the garage facade with lit showroom windows"></div>
<h2 class="banner-title">To Build Your<br>Luxury “Homes” For Cars!</h2>
<div class="btn" style="left:525px;top:1795px;width:150px;height:40px">Contact Us Today</div>

<h2 class="heading abs" style="left:0;width:1200px;text-align:center;top:2104px;font-size:26px"><span class="lite">Work</span> Gallery</h2>
<svg class="swoosh" style="left:570px;top:2142px" viewBox="0 0 60 8"><path d="M0 6 Q30 -2 60 4 Q30 2 0 8Z" fill="#0054AA"/></svg>
<div class="shot" style="left:187px;top:2171px;width:399px;height:228px;background:linear-gradient(160deg,#c9b79a,#5a3a30 60%,#b9bfc6)" role="img" aria-label="Two black and red hot rods in a workshop"></div>
<div class="shot" style="left:600px;top:2171px;width:412px;height:228px;background:linear-gradient(160deg,#3a2e2a,#7a6a30 50%,#1f1f22)" role="img" aria-label="Yellow and black hot rods in a dark garage"></div>
<div class="shot" style="left:187px;top:2416px;width:399px;height:229px;background:linear-gradient(160deg,#b9a488,#2a2f4a 55%,#cfd2d4)" role="img" aria-label="Two vintage touring cars in a showroom"></div>
<div class="shot" style="left:600px;top:2416px;width:412px;height:229px;background:linear-gradient(160deg,#4a4440,#2b2d33 50%,#8a8c92)" role="img" aria-label="Hot rods under construction in a large shop"></div>
<div class="btn" style="left:525px;top:2668px;width:149px;height:43px">View All</div>

<div class="abs contact-card"></div>
<svg class="abs" style="left:910px;top:3240px" width="36" height="36" viewBox="0 0 36 36"><path d="M36 0 L0 36 L36 36Z" fill="#fff"/><path d="M36 0 L0 36 L30 6Z" fill="#7BADD7"/></svg>
<h2 class="heading abs" style="left:254px;width:692px;text-align:center;top:2852px;font-size:26px"><span class="lite">Quick</span> Contact</h2>
<svg class="swoosh" style="left:570px;top:2890px" viewBox="0 0 60 8"><path d="M0 6 Q30 -2 60 4 Q30 2 0 8Z" fill="#0054AA"/></svg>
<p class="contact-sub">Send Us Your Details About Your Garage Or Contact Us<br>Directly At 123.456.7890</p>
<div class="field" style="left:317px;top:2981px;width:275px"><svg width="10" height="10" viewBox="0 0 10 10" fill="none" stroke="#0677BA"><circle cx="5" cy="3" r="2.2"/><path d="M1 10a4 4 0 0 1 8 0"/></svg>First Name</div>
<div class="field" style="left:607px;top:2981px;width:275px"><svg width="10" height="10" viewBox="0 0 10 10" fill="none" stroke="#0677BA"><circle cx="5" cy="3" r="2.2"/><path d="M1 10a4 4 0 0 1 8 0"/></svg>Last Name</div>
<div class="field" style="left:317px;top:3030px;width:275px"><svg width="11" height="9" viewBox="0 0 11 9" fill="none" stroke="#0677BA"><rect x=".5" y=".5" width="10" height="8"/><path d="M.5 .5 5.5 5 10.5 .5"/></svg>Email</div>
<div class="field" style="left:607px;top:3030px;width:275px"><svg width="10" height="10" viewBox="0 0 24 24" fill="none" stroke="#0677BA" stroke-width="2"><path d="M5 3h4l2 5-2.5 1.5a11 11 0 0 0 6 6L16 13l5 2v4a2 2 0 0 1-2 2A17 17 0 0 1 3 5a2 2 0 0 1 2-2z"/></svg>Phone</div>
<div class="field tall" style="left:317px;top:3079px;width:565px"><svg width="11" height="11" viewBox="0 0 11 11" fill="none" stroke="#0677BA"><circle cx="5.5" cy="5.5" r="4.8"/><path d="M3 5h5M3 7h3"/></svg>How Can We Help You?</div>
<div class="btn" style="left:522px;top:3182px;width:127px;height:34px;background:var(--blue-deep);font-size:12px;font-weight:600;border-radius:0">Submit Now</div>

<svg class="abs footer" viewBox="0 0 1200 488">
  <path d="M0 80 C 250 -10 500 0 750 60 C 950 110 1100 100 1200 40 L1200 488 L0 488Z" fill="#000"/>
  <path d="M0 70 C 250 -20 500 -10 750 45 C 950 95 1100 90 1200 30 L1200 55 C 1100 110 950 120 750 70 C 500 10 250 5 0 95Z" fill="#0054AA"/>
  <path d="M650 40 C 900 110 1080 110 1200 20 L1200 40 C 1080 120 900 120 650 40Z" fill="#29A8E0"/>
</svg>
<div class="brand" style="left:0;width:1200px;justify-content:center;top:3576px;font-size:28px;color:#fff"><span class="mark" style="width:40px;height:40px;background:#fff"></span>SUMMIT CARPORTS</div>
<div class="rule" style="top:3650px"></div>
<div class="foot-info" style="left:254px"><span class="ring"><svg width="16" height="20" viewBox="0 0 16 20" fill="none" stroke="#fff" stroke-width="1.4"><path d="M8 19s6-6.5 6-11A6 6 0 0 0 2 8c0 4.5 6 11 6 11z"/><circle cx="8" cy="8" r="2.2"/></svg></span><span>Street Name, City Name<br>State Zipcode</span></div>
<div class="foot-info" style="left:524px"><span class="ring"><svg width="18" height="18" viewBox="0 0 24 24" fill="none" stroke="#fff" stroke-width="1.6"><path d="M5 3h4l2 5-2.5 1.5a11 11 0 0 0 6 6L16 13l5 2v4a2 2 0 0 1-2 2A17 17 0 0 1 3 5a2 2 0 0 1 2-2z"/></svg></span><span>Call Us<br>123.456.7890</span></div>
<div class="foot-info" style="left:726px"><span class="ring"><svg width="18" height="14" viewBox="0 0 18 14" fill="none" stroke="#fff" stroke-width="1.4"><rect x=".7" y=".7" width="16.6" height="12.6"/><path d="M.7 .7 9 8l8.3-7.3"/></svg></span><span>Email Us<br>inquiry@summitcarports.com</span></div>
<div class="rule" style="top:3745px"></div>
<div class="social" style="left:536px"></div>
<div class="social" style="left:570px"></div>
<div class="social" style="left:604px"></div>
<div class="social" style="left:638px"></div>
<p class="abs" style="left:0;width:1200px;text-align:center;top:3812px;font-size:12px;color:#fff">Copyright 2022 Summit Carports. All Rights Reserved.</p>

</body>
</html>
```